Accounting firm needing business card / letterhead designed
Marcus L. Trenholm, CPA
marcus@veltrowledger.com
www.veltrowledger.com
842 E Alder Ave Perrysburg, OH 43827
419-562-0974

```html
<!DOCTYPE html>
<html lang="en">
<head>
<meta charset="utf-8">
<title>Veltrow Ledger – Business Card</title>
<link rel="stylesheet" href="https://fonts.googleapis.com/css2?family=Source+Sans+3:wght@400;600;700&display=swap">
<style>
  :root {
    --navy: #2b2568;
    --navy-soft: #37317a;
    --green: #7cc242;
    --white: #ffffff;
    --ink: #2b2568;
    --grey-text: #3a3a3a;
    --backdrop: #ecebe8;
  }
  * { box-sizing: border-box; margin: 0; padding: 0; }
  html, body {
    width: 1200px;
    height: 900px;
    overflow: hidden;
    background: var(--backdrop);
    font-family: "Source Sans 3", sans-serif;
  }
  .sheet {
    position: relative;
    width: 1200px;
    height: 900px;
  }
  .card {
    position: absolute;
    top: 296px;
    width: 540px;
    height: 309px;
    overflow: hidden;
    box-shadow: 0 6px 18px rgba(0,0,0,0.12);
  }
  /* Back side */
  .card-back {
    left: 40px;
    background: var(--navy);
  }
  .card-back .pattern-field {
    position: absolute;
    inset: 0;
    background: linear-gradient(135deg, var(--navy-soft), var(--navy));
  }
  .card-back .brand-mark {
    position: absolute;
    left: 0; right: 0;
    top: 50%;
    transform: translateY(-50%);
    text-align: center;
    color: var(--green);
    font-weight: 700;
    font-size: 30px;
    letter-spacing: 1px;
  }
  /* Front side */
  .card-front {
    left: 620px;
    background: var(--white);
  }
  .brand-name {
    position: absolute;
    left: 40px;
    top: 46px;
    color: var(--ink);
    font-weight: 700;
    font-size: 44px;
    letter-spacing: 1px;
    line-height: 1;
    text-transform: uppercase;
  }
  .address {
    position: absolute;
    right: 26px;
    top: 140px;
    text-align: right;
    color: var(--grey-text);
    font-size: 12.5px;
    line-height: 1.35;
  }
  .holder-name {
    position: absolute;
    left: 40px;
    top: 168px;
    color: var(--ink);
    font-weight: 700;
    font-size: 21px;
    text-transform: uppercase;
    letter-spacing: 0.3px;
  }
  .contact-list {
    position: absolute;
    left: 40px;
    top: 204px;
    list-style: none;
    color: var(--grey-text);
    font-size: 15px;
    line-height: 20px;
  }
  .contact-list li {
    display: flex;
    align-items: center;
    gap: 7px;
  }
  .contact-list svg { width: 12px; height: 12px; flex: none; }
  .base-band {
    position: absolute;
    left: 0; right: 0; bottom: 0;
    height: 26px;
    display: flex;
  }
  .base-band .band-navy { width: 63%; background: var(--navy); }
  .base-band .band-green { width: 37%; background: var(--green); }
</style>
</head>
<body>
<main class="sheet">
  <section class="card card-back" aria-label="Card back">
    <div class="pattern-field" role="img" aria-label="Repeating faint company name pattern on navy"></div>
    <div class="brand-mark">VELTROW</div>
  </section>

  <section class="card card-front" aria-label="Card front">
    <div class="brand-name">Veltrow Ledger</div>
    <address class="address">842 E Alder Ave Perrysburg,<br>OH 43827</address>
    <h1 class="holder-name">Marcus L. Trenholm, CPA</h1>
    <ul class="contact-list">
      <li>
        <svg viewBox="0 0 12 12" aria-hidden="true"><path d="M2.5 1 L4.5 1 L5.3 3.6 L4 4.6 Q5 7 7.4 8 L8.4 6.7 L11 7.5 L11 9.5 Q10.5 11 9 11 Q1 10 1 2.5 Q1 1 2.5 1 Z" fill="var(--green)"/></svg>
        419-562-0974
      </li>
      <li>
        <svg viewBox="0 0 12 12" aria-hidden="true"><rect x="0.5" y="2" width="11" height="8" fill="var(--green)"/><path d="M0.8 2.4 L6 6.6 L11.2 2.4" fill="none" stroke="#fff" stroke-width="1"/></svg>
        marcus@veltrowledger.com
      </li>
      <li>
        <svg viewBox="0 0 12 12" aria-hidden="true"><circle cx="6" cy="6" r="5.5" fill="var(--green)"/><path d="M0.8 6 H11.2 M6 0.6 Q3 6 6 11.4 M6 0.6 Q9 6 6 11.4" fill="none" stroke="#fff" stroke-width="0.8"/></svg>
        www.veltrowledger.com
      </li>
    </ul>
    <div class="base-band">
      <span class="band-navy"></span>
      <span class="band-green"></span>
    </div>
  </section>
</main>
</body>
</html>
```